Private Investment Firm Needs PowerPoint Presentation Template

Design PowerPoint template, take Pinebrook-submitted rough presentation draft, and drop it into new template. See attached Project Brief file for more detail.
Updates

Some decent designs have been submitted but they seem to lack the understanding of our target markets. I am hopeful that more time and feedback will result in better results.

Target Market(s)

Private company owners and intermediaries.

Font styles to use
Serif

Colors
3176b5

Requirements
Must have
• See attached Project Brief.
Nice to have
Should not have
• No B2C fluff--this is a B2B project.

```html
<!DOCTYPE html>
<html lang="en">
<head>
<meta charset="utf-8">
<title>Pinebrook – Introduction to Non-Control Capital</title>
<link href="https://fonts.googleapis.com/css2?family=Arimo:wght@400;700&display=swap" rel="stylesheet">
<style>
:root{
  --canvas:#ececec;
  --navy:#264a6f;
  --navy-deep:#1d3b5a;
  --blue:#1a6fc4;
  --blue-text:#1d6fbf;
  --ink:#333;
  --muted:#555;
  --rule:#9a9a9a;
  --cell-grey:#ececec;
  --white:#fff;
}
*{box-sizing:border-box;margin:0;padding:0}
html,body{width:1200px;height:1050px;overflow:hidden}
body{background:var(--canvas);font-family:"Arimo",Arial,sans-serif;color:var(--ink);position:relative}
.slide{position:absolute;width:556px;height:314px;background:var(--white);overflow:hidden}
.s1{left:21px;top:13px}.s2{left:618px;top:13px}
.s3{left:21px;top:335px}.s4{left:618px;top:335px}
.s5{left:21px;top:658px}.s6{left:618px;top:658px}
.abs{position:absolute}

.brand{position:absolute;display:flex;align-items:center;gap:6px;font-weight:700;letter-spacing:1.5px;color:var(--navy)}
.brand .dot{border-radius:50%;border:2px solid currentColor}
.brand-lg{font-size:14px}.brand-lg .dot{width:22px;height:22px}
.brand-sm{font-size:10px;right:18px;top:14px}.brand-sm .dot{width:17px;height:17px}
.brand-white{color:var(--white)}

.cover-band{position:absolute;left:0;top:63px;width:556px;height:247px;background:var(--navy)}
.cover-rule{position:absolute;left:0;top:304px;width:556px;height:6px;background:var(--blue)}
.cover-title{position:absolute;left:18px;color:var(--white);font-weight:700;font-size:34px;line-height:40px}
.cover-sub{position:absolute;left:18px;color:var(--white);font-size:9px;line-height:10.5px}
.cover-date{position:absolute;left:18px;color:var(--white);font-size:9px}
.s2{background:var(--navy)}
.s2 .backdrop{position:absolute;inset:0;background:linear-gradient(180deg,#2b4d72 0%,#2a4a6c 70%,#3c5c80 100%)}
.s2 .bridge{position:absolute;left:425px;top:0;width:131px;height:314px;background:linear-gradient(180deg,#7f97b8 0%,#5b7aa1 45%,#3a5d86 100%)}

.slide-title{position:absolute;left:17px;top:18px;font-size:18px;color:var(--ink)}
.title-rule{position:absolute;left:17px;right:18px;top:47px;height:1px;background:var(--rule)}
.lead{position:absolute;left:17px;top:63px;font-size:11.5px;font-weight:700;color:var(--blue-text)}
.check-row{position:absolute;display:flex;align-items:center;gap:8px;font-size:9.5px;color:var(--muted)}
.col-rule{position:absolute;width:1px;background:#ddd}
.col-text{position:absolute;width:130px;font-size:7.5px;line-height:9.8px;color:var(--muted);text-align:center}

.footer{position:absolute;left:0;top:296px;width:556px;height:14px}
.footer .bar{position:absolute;left:0;top:0;width:520px;height:14px;background:var(--blue)}
.footer .tip{position:absolute;left:500px;top:0}
.footer .mark{position:absolute;left:17px;top:3px;width:8px;height:8px;border-radius:50%;background:var(--white)}
.footer .label{position:absolute;left:31px;top:3.5px;font-size:5px;color:var(--white)}
.page-no{position:absolute;left:535px;top:300px;font-size:6px;color:var(--muted)}

.def-box{position:absolute;left:0;top:48px;width:556px;height:136px;background:var(--navy);color:var(--white)}
.def-lead{position:absolute;left:18px;top:15px;width:500px;font-size:11.5px;line-height:14px;font-weight:700}
.def-box .check-row{color:var(--white);font-size:10px}
.note{position:absolute;font-size:11.5px;line-height:14px;color:var(--muted);width:200px}
.note b{color:var(--blue-text)}

.s5 .backdrop{position:absolute;inset:0;background:linear-gradient(135deg,#3d5f86 0%,#2c4c72 45%,#1f3d60 100%)}
.quote-rule{position:absolute;top:86px;height:1px;background:rgba(255,255,255,.55)}
.quote-badge{position:absolute;left:243px;top:44px;width:70px;height:70px;border-radius:50%;border:2px solid var(--white);color:var(--white);font-size:40px;font-weight:700;text-align:center;line-height:78px;letter-spacing:-2px}
.quote{position:absolute;left:30px;top:128px;width:496px;text-align:center;color:var(--white);font-size:15px;line-height:18.3px}
.quote-name{position:absolute;left:0;width:556px;top:237px;text-align:center;color:var(--white);font-size:12px;font-weight:700}
.quote-org{position:absolute;left:0;width:556px;top:253px;text-align:center;color:var(--white);font-size:9px}

.uses{position:absolute;left:18px;top:65px;width:520px;display:grid;grid-template-columns:repeat(4,1fr);grid-template-rows:68px 69px 92px}
.use{padding:8px 6px 0;text-align:center;font-size:5.2px;line-height:6.6px;color:var(--muted)}
.use h3{font-size:7px;line-height:8px;font-weight:700;color:var(--ink);margin-bottom:2px}
.use.primary{background:var(--blue);color:var(--white);border-left:1px solid var(--white)}
.use.primary:first-child{border-left:0}
.use.primary h3{color:var(--white)}
.use.shaded{background:var(--cell-grey);border-left:1px solid var(--white);padding-top:11px}
.use.shaded:nth-child(9){border-left:0}
.use.plain{padding-top:13px}

.caption{position:absolute;left:18px;top:991px;font-size:43px;font-weight:700;color:#1f5585}
</style>
</head>
<body>

<!-- Cover, version A -->
<section class="slide s1">
  <div class="brand brand-sm"><span class="dot"></span>PINEBROOK</div>
  <div class="cover-band"></div>
  <div class="cover-rule"></div>
  <h1 class="cover-title" style="top:112px">Introduction to<br>Non-Control Capital</h1>
  <p class="cover-sub" style="top:199px">The Lower Middle Market Private Company Strategy for Raising Capital<br>While Maintaining Business Control</p>
  <p class="cover-date" style="top:225px">Fall 2018</p>
</section>

<!-- Cover, version B -->
<section class="slide s2">
  <div class="backdrop" role="img" aria-label="Blue-toned city waterfront skyline"></div>
  <div class="bridge" role="img" aria-label="Blue-toned suspension bridge tower over water"></div>
  <div class="brand brand-lg brand-white" style="left:18px;top:48px"><span class="dot"></span>PINEBROOK</div>
  <h1 class="cover-title" style="top:120px">Introduction to<br>Non-Control Capital</h1>
  <p class="cover-sub" style="top:204px">The Lower Middle Market Private Company Strategy<br>for Raising Capital. While Maintaining Business Control</p>
  <p class="cover-date" style="top:232px">Fall 2018</p>
</section>

<!-- Introduction -->
<section class="slide s3">
  <h2 class="slide-title">Introduction</h2>
  <div class="brand brand-sm"><span class="dot"></span>PINEBROOK</div>
  <div class="title-rule"></div>
  <p class="lead">Private company owners have traditionally considered two capital raising options:</p>
  <div class="check-row" style="left:17px;top:87px">
    <svg width="16" height="16" viewBox="0 0 16 16"><circle cx="8" cy="8" r="7" fill="none" stroke="#1d6fbf" stroke-width="1.2"/><path d="M4.5 8.2l2.3 2.3 4.6-4.8" fill="none" stroke="#1d6fbf" stroke-width="1.3"/></svg>
    Borrow from a local bank, or</div>
  <div class="check-row" style="left:17px;top:112px">
    <svg width="16" height="16" viewBox="0 0 16 16"><circle cx="8" cy="8" r="7" fill="none" stroke="#1d6fbf" stroke-width="1.2"/><path d="M4.5 8.2l2.3 2.3 4.6-4.8" fill="none" stroke="#1d6fbf" stroke-width="1.3"/></svg>
    Sell most or all of the company to a change-of-control investor (aka Buyout firm)</div>
  <div class="abs" style="left:17px;right:18px;top:146px;height:1px;background:#ddd"></div>
  <div class="col-rule" style="left:194px;top:158px;height:112px"></div>
  <div class="col-rule" style="left:359px;top:158px;height:112px"></div>

  <svg class="abs" style="left:76px;top:163px" width="36" height="38" viewBox="0 0 36 38" fill="none" stroke="#1d6fbf" stroke-width="1.4">
    <circle cx="18" cy="19" r="9"/><path d="M14 28v5h8v-5"/><path d="M18 2v4M4 19h4M28 19h4M8 9l3 3M28 9l-3 3"/>
    <path d="M21 15.5c-1-1.2-6-1.2-5 1.5s5 1 5 3.8-4.5 2-5.5 .8M18 13v12"/>
  </svg>
  <p class="col-text" style="left:29px;top:213px">An alternative must have not considered is the raising of Non-Control Capital, or capital that is invested into the business yet allows those same owners to retain controlling interest in their company</p>

  <svg class="abs" style="left:260px;top:165px" width="30" height="36" viewBox="0 0 30 36" fill="none" stroke="#1d6fbf" stroke-width="1.4">
    <circle cx="15" cy="10" r="7"/><path d="M2 35v-6c0-5 5-8 13-8s13 3 13 8v6z"/><path d="M15 21l-2 6 2 3 2-3z"/>
  </svg>
  <p class="col-text" style="left:210px;top:213px">Non-Control Capital is not appropriate for every private company owner but neither is a Change-of-Control sale</p>

  <svg class="abs" style="left:440px;top:167px" width="38" height="32" viewBox="0 0 38 32" fill="none" stroke="#1d6fbf" stroke-width="1.4">
    <path d="M2 8l7-5 6 4M36 8l-7-5-8 5-6 6 3 2 6-4"/><path d="M4 10l12 14c2 2 4 1 5 0l10-11M13 20l3 3M17 17l4 4M21 15l4 4"/>
  </svg>
  <p class="col-text" style="left:394px;top:213px">The key is to determine what the business and owners require, and then partner with an investor best aligned with those needs so that long-term company growth, and personal goals, can both be achieved</p>

  <div class="footer"><div class="bar"></div><svg class="tip" width="56" height="14"><polygon points="0,0 40,0 54,14 14,14" fill="#1d3b5a"/></svg><span class="mark"></span><span class="label">Confidential</span></div>
  <span class="page-no">3</span>
</section>

<!-- Definition -->
<section class="slide s4">
  <h2 class="slide-title">What is Non-Control Capital?</h2>
  <div class="brand brand-sm"><span class="dot"></span>PINEBROOK</div>
  <div class="def-box">
    <p class="def-lead">Non-Control Capital is an investment which is primarily used for the ongoing operation and/or growth of a business but also allows the current owners to retain:</p>
    <div class="check-row" style="left:18px;top:61px"><svg width="18" height="18" viewBox="0 0 16 16"><circle cx="8" cy="8" r="7" fill="none" stroke="#fff" stroke-width="1.1"/><path d="M4.5 8.2l2.3 2.3 4.6-4.8" fill="none" stroke="#fff" stroke-width="1.2"/></svg>Control of the business economics</div>
    <div class="check-row" style="left:302px;top:61px"><svg width="18" height="18" viewBox="0 0 16 16"><circle cx="8" cy="8" r="7" fill="none" stroke="#fff" stroke-width="1.1"/><path d="M4.5 8.2l2.3 2.3 4.6-4.8" fill="none" stroke="#fff" stroke-width="1.2"/></svg>Control of strategy and key decision making</div>
    <div class="check-row" style="left:18px;top:98px"><svg width="18" height="18" viewBox="0 0 16 16"><circle cx="8" cy="8" r="7" fill="none" stroke="#fff" stroke-width="1.1"/><path d="M4.5 8.2l2.3 2.3 4.6-4.8" fill="none" stroke="#fff" stroke-width="1.2"/></svg>Control of the business operations</div>
    <div class="check-row" style="left:302px;top:98px"><svg width="18" height="18" viewBox="0 0 16 16"><circle cx="8" cy="8" r="7" fill="none" stroke="#fff" stroke-width="1.1"/><path d="M4.5 8.2l2.3 2.3 4.6-4.8" fill="none" stroke="#fff" stroke-width="1.2"/></svg>Control of the Board of Directors</div>
  </div>
  <div class="col-rule" style="left:256px;top:198px;height:74px"></div>
  <svg class="abs" style="left:22px;top:217px" width="34" height="40" viewBox="0 0 34 40" fill="none" stroke="#1d6fbf" stroke-width="1.5">
    <path d="M3 2h18l7 7v16M3 2v34h16"/><path d="M8 12h12M8 17h14M8 22h10"/><circle cx="26" cy="31" r="7" fill="#1d6fbf"/><path d="M22.5 31l2.5 2.5 4.5-4.5" stroke="#fff"/>
  </svg>
  <p class="note" style="left:66px;top:217px">Requires the <b>alignment of management</b> incentives with ownership</p>
  <svg class="abs" style="left:292px;top:217px" width="34" height="40" viewBox="0 0 34 40" fill="none" stroke="#1d6fbf" stroke-width="1.5">
    <rect x="8" y="3" width="24" height="30"/><path d="M12 2h16v4H12z"/><path d="M17 13l2 2 3-3M24 14h5M17 21l2 2 3-3M24 22h5"/><circle cx="6" cy="25" r="3"/><path d="M1 38c0-5 2-8 5-8s5 3 5 8"/>
  </svg>
  <p class="note" style="left:334px;top:217px;width:205px">In essence, a company <b>receives the capital it needs</b> to implement its business plans but owners continue to retain ultimate control</p>
  <div class="footer"><div class="bar"></div><svg class="tip" width="56" height="14"><polygon points="0,0 40,0 54,14 14,14" fill="#1d3b5a"/></svg><span class="mark"></span><span class="label">Confidential</span></div>
  <span class="page-no">4</span>
</section>

<!-- Owner quote -->
<section class="slide s5">
  <div class="backdrop" role="img" aria-label="Blue-toned photo of business people in suits"></div>
  <div class="quote-rule" style="left:17px;width:226px"></div>
  <div class="quote-rule" style="left:313px;width:225px"></div>
  <div class="quote-badge">“”</div>
  <p class="quote">Our company had several business opportunities but I needed outside capital to take advantage of them. Why would I cede control of my business when we were at the exact point when raising outside capital would allow me to accelerate growth and achieve my life-long business and personal goals?!</p>
  <p class="quote-name">Daniel Harper, CEO</p>
  <p class="quote-org">The Kestrel Group</p>
</section>

<!-- Uses table -->
<section class="slide s6">
  <h2 class="slide-title">The 12 Primary Uses of Non-Control Capital</h2>
  <div class="brand brand-sm"><span class="dot"></span>PINEBROOK</div>
  <div class="uses">
    <div class="use primary"><h3>Growth</h3>Capital used to organically expand a business: introduce new products, build a new factory, hire additional management or employees, enter new markets, or for general working capital purposes</div>
    <div class="use primary"><h3>Acquisitions</h3>Capital used to acquire one or more competitors or to allow for further vertical or horizontal integration</div>
    <div class="use primary"><h3>Partner or Shareholder Buy-Out</h3>Capital used to buy-out an inactive or retiring partner or shareholder</div>
    <div class="use primary"><h3>Management Buy-Out (MBO)</h3>When the incumbent management team buys most or all of the ownership of an inactive founder or executive</div>
    <div class="use plain"><h3>Management Buy-In (MBI)</h3>When an external, experienced executive buys a business from one or more inactive owners and needs additional capital to afford the purchase</div>
    <div class="use plain"><h3>Family Ownership &amp; Wealth Transfer</h3>When junior generations of a family acquire most or all of the ownership interests of more senior generations allowing the business to remain in the family name</div>
    <div class="use plain"><h3>Balance Sheet Recapitalization</h3>Changes the debt and equity mixture of a Company's finances to a more optimal capital structure</div>
    <div class="use plain"><h3>Refinancing</h3>Replacing one form or type of debt with another with better terms, conditions, and flexibility</div>
    <div class="use shaded"><h3>Family Office Support</h3>Allows a Family Office to affect an investment in a Company by allowing a junior capital provider to invest alongside them</div>
    <div class="use shaded"><h3>Senior Lender Enhancement<br>or Transition</h3>When a Company has grown beyond the means or interest of its senior bank but needs additional capital to support its continuing growth</div>
    <div class="use shaded"><h3>De-Lever Balance Sheet</h3>When a Company has taken on too much debt (typically senior debt) and replaces some of it with either equity or other junior capital to provide operating flexibility</div>
    <div class="use shaded"><h3>Owner Dividend (Liquidity)</h3>When one or more owners take a non-life changing cash distribution, typically used to diversify their net worth</div>
  </div>
  <div class="footer"><div class="bar"></div><svg class="tip" width="56" height="14"><polygon points="0,0 40,0 54,14 14,14" fill="#1d3b5a"/></svg><span class="mark"></span><span class="label">Confidential</span></div>
  <span class="page-no">6</span>
</section>

<p class="caption">Pinebrook - First Part</p>

</body>
</html>
```